Maple Roster Business Card for recruitment company

We are looking for a Business Card Design that incorporates our personal details and our busines name and logo. We are a specialized search consultancy that recruit Property and Construction professionals.
We would like a business card that stands out and is appealing to the Construction and Property industry as well.

Target Market(s)

people in the construction and property industry

Contact Information for Business Card

Business Name and logo

Font styles to use
Serif

Colors
0094D4
00A9DD
6FCCEA
C7EBF8
E9F6FB

Requirements
Must have
• Business name and logo as well as contact details
Should not have
• No photos of us please

```html
<!DOCTYPE html>
<html lang="en">
<head>
<meta charset="utf-8">
<title>Maple Roster Business Card</title>
<link href="https://fonts.googleapis.com/css2?family=Lato:wght@400;700&display=swap" rel="stylesheet">
<style>
  :root {
    --backdrop: #1c1d1f;
    --teal: #154a5c;
    --teal-deep: #0e3a49;
    --teal-seam: #1f5668;
    --paper: #f7f8f8;
    --white: #ffffff;
  }
  * { margin: 0; padding: 0; box-sizing: border-box; }
  html, body {
    width: 1200px; height: 874px; overflow: hidden;
    background: var(--backdrop);
    font-family: "Lato", sans-serif;
  }
  .canvas { position: relative; width: 1200px; height: 874px; }
  .card {
    position: absolute; left: 320px; width: 560px; height: 320px;
    border-radius: 18px; overflow: hidden;
  }
  .card-back { top: 105px; background: var(--teal); }
  .card-front { top: 449px; background: var(--paper); }

  .pattern-field {
    position: absolute; inset: 0;
    background: linear-gradient(120deg, #4c7584 0%, var(--teal) 45%, var(--teal-deep) 100%);
  }
  .back-brand {
    position: absolute; right: 26px; bottom: 24px;
    display: flex; align-items: center; gap: 10px;
    color: var(--white); font-size: 15px; font-weight: 400;
    letter-spacing: 2px; text-transform: uppercase;
  }
  .brand-dot {
    width: 14px; height: 14px; border-radius: 50%;
    background: currentColor; flex: none;
  }

  .front-art { position: absolute; inset: 0; }
  .contact {
    position: absolute; left: 42px; top: 120px; color: var(--white);
  }
  .contact-name {
    font-size: 19px; font-weight: 700; letter-spacing: 0.5px; text-transform: uppercase;
  }
  .contact-role { font-size: 13px; margin-bottom: 14px; }
  .contact-address { font-size: 13px; line-height: 17px; margin-bottom: 10px; }
  .contact-list { list-style: none; font-size: 13px; line-height: 17px; }
  .contact-list li { display: flex; align-items: center; gap: 8px; }
  .contact-list svg { width: 11px; height: 11px; flex: none; }
  .wordmark {
    position: absolute; left: 290px; top: 90px;
    display: flex; align-items: center; gap: 10px; white-space: nowrap;
    color: var(--teal); font-size: 27px; font-weight: 400;
    letter-spacing: 3px; line-height: 36px; text-transform: uppercase;
  }
</style>
</head>
<body>
<main class="canvas">
  <section class="card card-back">
    <div class="pattern-field" role="img" aria-label="Repeating pattern of the brand mark in metallic tones"></div>
    <p class="back-brand"><span class="brand-dot"></span>Maple Roster</p>
  </section>

  <section class="card card-front">
    <svg class="front-art" viewBox="0 0 560 320">
      <polygon points="0,0 212,0 330,320 0,320" fill="var(--teal)"/>
      <polygon points="212,0 234,0 352,320 330,320" fill="var(--teal-seam)" role="img" aria-label="Zipper seam ornament along the diagonal edge"/>
    </svg>

    <div class="contact">
      <p class="contact-name">Daniel Hart</p>
      <p class="contact-role">President</p>
      <p class="contact-address">412 Birchwood Road<br>Fairbanks, Alaska 34590</p>
      <ul class="contact-list">
        <li><svg viewBox="0 0 12 12"><path d="M2 1l2.5 0 1 3-1.5 1a7 7 0 0 0 3 3l1-1.5 3 1V10.5a1 1 0 0 1-1 1A9.5 9.5 0 0 1 .5 2a1 1 0 0 1 1.5-1z" fill="#fff"/></svg>555-214-7730</li>
        <li><svg viewBox="0 0 12 12"><rect x="3" y="0.5" width="6" height="11" rx="1" fill="none" stroke="#fff"/><circle cx="6" cy="9.5" r="0.8" fill="#fff"/></svg>555-318-6042</li>
        <li><svg viewBox="0 0 12 12"><rect x="1" y="4" width="10" height="6" rx="1" fill="#fff"/><rect x="3" y="1" width="6" height="3" fill="#fff"/></svg>555-427-1985</li>
        <li><svg viewBox="0 0 12 12"><rect x="0.5" y="2.5" width="11" height="7" fill="#fff"/><path d="M0.5 2.5L6 7l5.5-4.5" fill="none" stroke="var(--teal)"/></svg>daniel@mapleroster.com</li>
        <li><svg viewBox="0 0 12 12"><circle cx="6" cy="6" r="5.5" fill="#fff"/><path d="M0.5 6h11M6 0.5c-3 3-3 8 0 11M6 0.5c3 3 3 8 0 11" fill="none" stroke="var(--teal)" stroke-width="0.8"/></svg>www.mapleroster.com</li>
      </ul>
    </div>

    <p class="wordmark"><span class="brand-dot"></span>Maple Roster</p>
  </section>
</main>
</body>
</html>
```